New Business Card Design Project

I need a design for business cards, i am an electrical business called "Corvane Electrical and Communications" i need the cards to be double sided with the company logo on the back (attached) the front needs to say my company name, web site, email address, telephone number, and ABN number and electrical license number. I am open to different arrangements of the information but would like the background to be incorporating something electrical or something that looks smart. open to all additional ideas also.

The company colours are orange and grey see logo attached.

Business Name: Corvane Electrical and Communications
Website: corvaneelectricalandcomms.example.com.au
Email: brent@corvaneelectricalandcomms.example.com.au
Telephone(mobile): 0481209736
ABN: 71208349162
Lic No: 418273D

Target Market(s)

Business entities, Project Managers, Accounts, Clients

Industry/Entity Type

Electrician

Contact Information for Business Card

I need a design for business cards, i am an electrical business called "Corvane Electrical and Communications" i need the cards to be double sided with the company logo on the back (attached) the front needs to say my company name

Font styles to use
Serif
Sans Serif

Colors
f37122
5c5c5c

Requirements
Must have
• Must have the Logo on the back open to different ways of it being on the back but had in mind to keep it central but again open to other options
Nice to have
• A real modern cool background that is eye catching yet contemporary
Should not have
• No backgrounds of a light bulb or plug or anything like that

```html
<!DOCTYPE html>
<html lang="en">
<head>
<meta charset="utf-8">
<title>Corvane Electrical and Communications – Business Card</title>
<link rel="stylesheet" href="https://fonts.googleapis.com/css2?family=Exo+2:wght@400;500;600&display=swap">
<style>
  :root {
    --orange: #f37122;
    --grey: #5c5c5c;
    --charcoal: #2f2f2f;
    --charcoal-deep: #262626;
    --frost: #e9e8e6;
    --frost-shade: #d6d4d1;
    --ink: #2e2e2e;
    --title-grey: #c9c9c9;
    --backdrop: #d8d5d0;
  }
  * { margin: 0; padding: 0; box-sizing: border-box; }
  html, body {
    width: 1200px;
    height: 969px;
    overflow: hidden;
    background: var(--backdrop);
    font-family: "Exo 2", "Trebuchet MS", sans-serif;
  }
  .card {
    position: absolute;
    left: 100px;
    top: 200px;
    width: 1000px;
    height: 570px;
    border-radius: 30px;
    overflow: hidden;
    box-shadow: 0 18px 40px rgba(0,0,0,0.18);
  }
  .card-backdrop {
    position: absolute;
    inset: 0;
    background: linear-gradient(165deg,
      var(--charcoal) 0%,
      var(--charcoal-deep) 42%,
      var(--grey) 52%,
      var(--frost-shade) 62%,
      var(--frost) 100%);
  }
  .brand {
    position: absolute;
    left: 58px;
    top: 118px;
    display: flex;
    align-items: center;
    gap: 18px;
    color: #f1f1f1;
  }
  .brand-dot {
    width: 26px;
    height: 26px;
    border-radius: 50%;
    background: var(--orange);
    flex: none;
  }
  .brand-name {
    font-weight: 500;
    font-size: 74px;
    line-height: 1;
    letter-spacing: 4px;
  }
  .brand-tagline {
    position: absolute;
    left: 102px;
    top: 224px;
    font-weight: 500;
    font-size: 19.5px;
    letter-spacing: 1.4px;
    color: #f1f1f1;
  }
  .person {
    position: absolute;
    right: 45px;
    top: 46px;
    text-align: right;
  }
  .person-name {
    font-weight: 600;
    font-size: 36px;
    letter-spacing: 1.5px;
    color: var(--orange);
    line-height: 1.1;
  }
  .person-role {
    font-weight: 400;
    font-size: 23px;
    letter-spacing: 0.5px;
    color: var(--title-grey);
    margin-top: 8px;
  }
  .credentials {
    position: absolute;
    right: 45px;
    top: 332px;
    text-align: right;
    color: var(--ink);
    font-size: 25px;
    line-height: 32px;
  }
  .contact-list {
    position: absolute;
    right: 34px;
    top: 410px;
    list-style: none;
    color: var(--ink);
  }
  .contact-list li {
    display: flex;
    justify-content: flex-end;
    align-items: center;
    gap: 14px;
    height: 41px;
  }
  .contact-phone { font-size: 25px; }
  .contact-email, .contact-web { font-size: 20px; }
  .contact-icon { width: 24px; height: 24px; flex: none; }
</style>
</head>
<body>
  <div class="card">
    <div class="card-backdrop" role="img" aria-label="Decorative orange and grey wave band dividing the dark upper area from the light lower area"></div>

    <div class="brand">
      <span class="brand-dot"></span>
      <span class="brand-name">CORVANE</span>
    </div>
    <div class="brand-tagline">ELECTRICAL &amp; COMMUNICATIONS</div>

    <div class="person">
      <div class="person-name">BRENT MARLOW</div>
      <div class="person-role">CEO/FOUNDER</div>
    </div>

    <div class="credentials">
      <div>ABN: 71208349162</div>
      <div>Lic No: 418273D</div>
    </div>

    <ul class="contact-list">
      <li class="contact-phone">
        <span>0481209736</span>
        <svg class="contact-icon" viewBox="0 0 24 24" aria-hidden="true">
          <rect x="6" y="2" width="12" height="20" rx="2" fill="none" stroke="var(--orange)" stroke-width="2.4"/>
          <circle cx="12" cy="18" r="1.3" fill="var(--orange)"/>
        </svg>
      </li>
      <li class="contact-email">
        <span>brent@corvaneelectricalandcomms.example.com.au</span>
        <svg class="contact-icon" viewBox="0 0 24 24" aria-hidden="true">
          <rect x="2" y="5" width="20" height="14" rx="1.5" fill="var(--orange)"/>
          <path d="M3,6 L12,13 L21,6" fill="none" stroke="#fff" stroke-width="1.6"/>
        </svg>
      </li>
      <li class="contact-web">
        <span>www.corvaneelectricalandcomms.example.com.au</span>
        <svg class="contact-icon" viewBox="0 0 24 24" aria-hidden="true">
          <circle cx="12" cy="12" r="10" fill="var(--orange)"/>
          <ellipse cx="12" cy="12" rx="4.5" ry="10" fill="none" stroke="#fff" stroke-width="1.3"/>
          <path d="M2,12 H22" stroke="#fff" stroke-width="1.3"/>
        </svg>
      </li>
    </ul>
  </div>
</body>
</html>
```